Retractable banner.
Health Check For Pets
Check for Ear Mites
Skin Health
Fleas & Ticks

A space SERVE BY <NAME OF CLINIC>

Ideally contain pictures of cats and dogs

```html
<!DOCTYPE html>
<html lang="en">
<head>
<meta charset="UTF-8">
<title>Health Check for Pets – Retractable Banner</title>
<link href="https://fonts.googleapis.com/css2?family=Montserrat:wght@600;700;800;900&display=swap" rel="stylesheet">
<style>
  :root {
    --red: #d12e36;
    --ink: #3a3a3c;
    --white: #ffffff;
    --stage: #e6e6e8;
    --logo-grey: #cfcfd1;
    --logo-text: #9c9c9e;
    --tan: #f2d3a3;
    --fur-dark: #4a4a4d;
    --dog-brown: #c9682f;
    --dog-cream: #f6dcc4;
  }
  * { margin: 0; padding: 0; box-sizing: border-box; }
  html, body { width: 1200px; height: 667px; overflow: hidden; }
  body {
    background: var(--stage);
    font-family: 'Montserrat', Arial, sans-serif;
    position: relative;
  }
  .banner {
    position: absolute;
    left: 0; top: 33px;
    width: 1200px; height: 600px;
    background: var(--white);
    overflow: hidden;
  }
  .kicker {
    position: absolute; left: 68px; top: 34px;
    color: var(--red); font-weight: 800; font-size: 41px; letter-spacing: 0.2px;
  }
  .headline {
    position: absolute; left: 62px; top: 58px;
    color: var(--ink); font-weight: 900; font-size: 156px; letter-spacing: -4px; line-height: 1;
  }
  .band { position: absolute; left: 0; top: 234px; }
  .checklist {
    position: absolute; left: 68px; top: 244px;
    color: var(--white); list-style: none;
  }
  .checklist-title { font-weight: 600; font-size: 40px; line-height: 48px; margin-bottom: 0; }
  .checklist li {
    display: flex; align-items: center; gap: 8px;
    font-weight: 600; font-size: 40px; line-height: 48px;
  }
  .checklist li svg { width: 32px; height: 32px; flex: none; }
  .served {
    position: absolute; left: 68px; top: 483px; width: 592px;
    display: flex; align-items: center; gap: 8px;
    color: var(--ink); font-weight: 800; font-size: 24px;
  }
  .served::before, .served::after {
    content: ""; flex: 1; height: 3px; background: var(--ink);
  }
  .clinic-name {
    position: absolute; left: 68px; top: 508px;
    color: var(--red); font-weight: 800; font-size: 50px; letter-spacing: -0.3px; white-space: nowrap;
  }
  .zoom { position: absolute; left: 520px; top: 95px; }
  .dog-art { position: absolute; left: 825px; top: 263px; }
  .logo-spot {
    position: absolute; left: 947px; top: 40px;
    width: 190px; height: 190px; border-radius: 50%;
    background: var(--logo-grey);
    display: flex; align-items: center; justify-content: center; text-align: center;
    color: var(--logo-text); font-weight: 800; font-size: 36px; line-height: 42px;
  }
</style>
</head>
<body>
  <main class="banner">
    <p class="kicker">HEALTH CHECK FOR</p>
    <h1 class="headline">PETS</h1>

    <svg class="band" width="620" height="230" viewBox="0 0 620 230" aria-hidden="true">
      <polygon points="0,0 526,0 609,230 0,230" fill="var(--red)"/>
    </svg>

    <ul class="checklist">
      <li class="checklist-title">CHECK FO</li>
      <li><svg viewBox="0 0 32 32" aria-hidden="true"><circle cx="15" cy="17" r="12" fill="none" stroke="#fff" stroke-width="3"/><polyline points="9,16 14,21 27,6" fill="none" stroke="#fff" stroke-width="3.5" stroke-linecap="round" stroke-linejoin="round"/></svg>EAR MITES</li>
      <li><svg viewBox="0 0 32 32" aria-hidden="true"><circle cx="15" cy="17" r="12" fill="none" stroke="#fff" stroke-width="3"/><polyline points="9,16 14,21 27,6" fill="none" stroke="#fff" stroke-width="3.5" stroke-linecap="round" stroke-linejoin="round"/></svg>SKIN HEALTH</li>
      <li><svg viewBox="0 0 32 32" aria-hidden="true"><circle cx="15" cy="17" r="12" fill="none" stroke="#fff" stroke-width="3"/><polyline points="9,16 14,21 27,6" fill="none" stroke="#fff" stroke-width="3.5" stroke-linecap="round" stroke-linejoin="round"/></svg>FLEAS &amp; TICKS</li>
    </ul>

    <p class="served">SERVE BY:</p>
    <p class="clinic-name">Pet Health Care CLINIC</p>

    <svg class="zoom" width="440" height="400" viewBox="0 0 440 400" role="img" aria-label="Magnified view of a tick on a pet's skin among dark fur">
      <defs>
        <linearGradient id="skinFur" x1="0" y1="0" x2="0.4" y2="1">
          <stop offset="0" stop-color="#a9a8d8"/>
          <stop offset="0.35" stop-color="var(--fur-dark)"/>
          <stop offset="0.75" stop-color="#8a6d52"/>
          <stop offset="1" stop-color="var(--tan)"/>
        </linearGradient>
      </defs>
      <polygon points="330,300 431,321 393,378" fill="var(--red)"/>
      <circle cx="195" cy="195" r="183" fill="url(#skinFur)" stroke="var(--red)" stroke-width="6"/>
    </svg>

    <svg class="dog-art" width="360" height="283" viewBox="0 0 360 283" role="img" aria-label="Illustration of a worried beagle puppy sitting, scratching">
      <defs>
        <linearGradient id="dogTone" x1="0" y1="0" x2="0" y2="1">
          <stop offset="0" stop-color="var(--dog-brown)"/>
          <stop offset="1" stop-color="var(--dog-cream)"/>
        </linearGradient>
      </defs>
      <ellipse cx="180" cy="266" rx="178" ry="15" fill="#e9a0c8"/>
      <rect x="110" y="0" width="190" height="270" rx="90" fill="url(#dogTone)"/>
    </svg>

    <div class="logo-spot">your<br>logo<br>here</div>
  </main>
</body>
</html>
```